Card Design for my dog training business Brightpaw Obedience

Need a business card design for my dog training business with my new logo. Want the card to come off professional yet fun. Want it to be very eye catchy as well. I normally have these at vet clinics, pet stores, and groomers. so need it to look better than my competitors.
Target Market(s)
dog owners
Industry/Entity Type
Dog Training
Contact Information for Business Card
needs logo, my name and info
Font styles to use
Serif
Colors
0255a3
ffffff
ec1f27
000000
333333
fbfbfb
Requirements
Must have
- Brightpaw Obedience
- Felix Orland
- 415 903 2276
- info@brightpawobedience.example
- www.brightpawobedience.example

```html
<!DOCTYPE html>
<html lang="en">
<head>
<meta charset="utf-8">
<title>Brightpaw Obedience – Business Card</title>
<link rel="stylesheet" href="https://fonts.googleapis.com/css2?family=EB+Garamond:ital,wght@0,500;1,400&family=Noto+Serif&family=Open+Sans&display=swap">
<style>
  :root {
    --brand-blue: #0255a3;
    --brand-red: #ec1f27;
    --paper: #fbfbfb;
    --white: #ffffff;
    --ink: #333333;
    --black: #000000;
    --backdrop: #b4b4b4;
  }
  * { box-sizing: border-box; margin: 0; padding: 0; }
  html, body { width: 1200px; height: 576px; overflow: hidden; }
  body { background: var(--backdrop); position: relative; }

  .card {
    position: absolute;
    top: 138px;
    width: 484px;
    height: 294px;
    border-radius: 10px;
    overflow: hidden;
    background: var(--paper);
    box-shadow: 0 3px 6px rgba(0,0,0,0.25);
  }
  .card--front { left: 82px; }
  .card--back  { left: 602px; }

  .wordmark {
    position: absolute;
    font-family: "EB Garamond", serif;
    font-weight: 500;
    font-size: 26px;
    line-height: 1.1;
    text-align: center;
    letter-spacing: 0.5px;
  }
  .card--front .wordmark { left: 0; right: 0; top: 106px; color: var(--ink); }

  .tagline-band {
    position: absolute;
    left: 0; right: 0;
    top: 256px;
    height: 28px;
    background: var(--brand-blue);
    color: var(--white);
    font-family: "EB Garamond", serif;
    font-style: italic;
    font-size: 13px;
    line-height: 28px;
    text-align: center;
  }

  .back-shape { position: absolute; inset: 0; width: 100%; height: 100%; }

  .holder { position: absolute; left: 26px; top: 42px; color: var(--white); }
  .holder-name { font-family: "Noto Serif", serif; font-size: 21px; line-height: 1.2; }
  .holder-role { font-family: "Open Sans", sans-serif; font-size: 12px; margin-top: 3px; }

  .contact-list {
    position: absolute; left: 26px; top: 208px;
    list-style: none;
    color: var(--white);
    font-family: "Open Sans", sans-serif;
    font-size: 12px;
  }
  .contact-item { display: flex; align-items: center; height: 19px; }
  .contact-icon { width: 11px; height: 11px; margin-right: 10px; fill: var(--white); }

  .card--back .wordmark {
    left: 290px; width: 176px; top: 106px;
    color: var(--brand-blue);
    font-size: 22px;
  }
</style>
</head>
<body>
  <section class="card card--front" aria-label="Card front">
    <div class="wordmark">Brightpaw<br>Obedience</div>
    <div class="tagline-band">“Training dogs across Texas one dog at a time.”</div>
  </section>

  <section class="card card--back" aria-label="Card back">
    <svg class="back-shape" viewBox="0 0 484 294" preserveAspectRatio="none" aria-hidden="true">
      <rect width="484" height="294" fill="var(--paper)"/>
      <path d="M0 0 H286 Q230 147 286 294 H0 Z" fill="var(--brand-red)"/>
      <path d="M0 0 H280 Q224 147 280 294 H0 Z" fill="var(--brand-blue)"/>
      <path d="M0 34 Q10 64 0 94 Z" fill="var(--brand-red)"/>
    </svg>

    <div class="holder">
      <div class="holder-name">Felix Orland</div>
      <div class="holder-role">Dog Trainer</div>
    </div>

    <ul class="contact-list">
      <li class="contact-item">
        <svg class="contact-icon" viewBox="0 0 12 12" aria-hidden="true"><path d="M1 3 Q6 0 11 3 L10 5 L8 4.5 L8 3.5 Q6 3 4 3.5 L4 4.5 L2 5 Z M2.5 6 H9.5 L10.5 11 H1.5 Z"/></svg>
        415 903 2276
      </li>
      <li class="contact-item">
        <svg class="contact-icon" viewBox="0 0 12 12" aria-hidden="true"><path d="M1 2.5 H11 V9.5 H1 Z M1.8 3.3 L6 6.6 L10.2 3.3" stroke="var(--blue,#0255a3)" stroke-width="0.8"/></svg>
        info@brightpawobedience.example
      </li>
      <li class="contact-item">
        <svg class="contact-icon" viewBox="0 0 12 12" aria-hidden="true"><circle cx="6" cy="6" r="5.2"/><path d="M1 6 H11 M6 0.8 Q3 6 6 11.2 M6 0.8 Q9 6 6 11.2" stroke="#0255a3" stroke-width="0.7" fill="none"/></svg>
        www.brightpawobedience.example
      </li>
    </ul>

    <div class="wordmark">Brightpaw<br>Obedience</div>
  </section>
</body>
</html>
```